Thornvale Group needs a business card design

We need a new business card design using the logo recently selected in a logo competition on Pixel Bazaar. Our business is a consultancy specializing in aviation and energy and the winning business card design will promote an image of precision and professionalism with creativity.

Please use the logo with the name on the front of the card and use a complementary font. Make the back white with either the light grey or dark grey logo.

Target Market(s)

Senior finance and legal leaders at aviation and energy companies

Industry/Entity Type

Management Consulting

Contact Information for Business Card

Peter Castrell
President
Thornvale Group

www.thornvalegroup.example

(555) 204-6391
pc@thornvalegroup.example

Requirements
Must have
• Professional font that goes well with the logo font

```html
<!DOCTYPE html>
<html lang="en">
<head>
<meta charset="utf-8">
<title>Thornvale Group — Business Card</title>
<link rel="stylesheet" href="https://fonts.googleapis.com/css2?family=Open+Sans:wght@400;600;700&display=swap">
<style>
  :root {
    --navy: #0f3f73;
    --ink: #111418;
    --paper: #ffffff;
    --backdrop: #e6e8eb;
    --card-shadow: rgba(20, 28, 40, 0.18);
  }
  * { box-sizing: border-box; margin: 0; padding: 0; }
  html, body {
    width: 1200px;
    height: 864px;
    overflow: hidden;
    background: var(--backdrop);
    font-family: "Open Sans", Arial, sans-serif;
  }
  .sheet {
    position: relative;
    width: 1200px;
    height: 864px;
  }
  .card {
    position: absolute;
    left: 320px;
    width: 560px;
    height: 320px;
    background: var(--paper);
    box-shadow: 0 6px 20px var(--card-shadow);
    overflow: hidden;
  }
  .card--front { top: 72px; }
  .card--back  { top: 472px; }

  /* Front */
  .front-mark {
    position: absolute;
    top: 44px;
    left: 258px;
    width: 44px;
    height: 44px;
    background: var(--navy);
  }
  .front-brand {
    position: absolute;
    top: 104px;
    left: 0;
    width: 100%;
    text-align: center;
    color: var(--navy);
    font-weight: 400;
    font-size: 36px;
    letter-spacing: 2px;
    line-height: 1.2;
  }
  .front-tagline {
    position: absolute;
    top: 182px;
    width: 100%;
    text-align: center;
    color: var(--navy);
    font-weight: 600;
    font-size: 18px;
  }
  .front-sectors {
    position: absolute;
    top: 214px;
    width: 100%;
    text-align: center;
    color: var(--ink);
    font-weight: 600;
    font-size: 13px;
  }

  /* Back */
  .back-brand {
    position: absolute;
    top: 30px;
    left: 40px;
    color: var(--navy);
    font-weight: 400;
    font-size: 32px;
    letter-spacing: 2px;
    line-height: 1.2;
  }
  .brand-field {
    position: absolute;
    left: 330px;
    top: 130px;
    width: 230px;
    height: 190px;
    background: var(--navy);
  }
  .person {
    position: absolute;
    top: 168px;
    left: 46px;
  }
  .person__name {
    color: var(--navy);
    font-weight: 700;
    font-size: 20px;
    line-height: 1.1;
  }
  .person__role {
    color: var(--ink);
    font-size: 13px;
  }
  .contact {
    position: absolute;
    top: 228px;
    left: 40px;
    list-style: none;
    color: var(--ink);
    font-size: 15px;
  }
  .contact__item {
    display: flex;
    align-items: center;
    gap: 10px;
    margin-bottom: 8px;
  }
  .contact__icon {
    width: 12px;
    height: 12px;
    fill: var(--navy);
    flex: none;
  }
</style>
</head>
<body>
<main class="sheet">
  <section class="card card--front" aria-label="Card front">
    <div class="front-mark" aria-hidden="true"></div>
    <div class="front-brand">Thornvale Group</div>
    <p class="front-tagline">Finance and Strategy Consulting</p>
    <p class="front-sectors">Aviation - Manufacturing - Energy</p>
  </section>

  <section class="card card--back" aria-label="Card back">
    <div class="back-brand">Thornvale Group</div>
    <div class="brand-field" role="img" aria-label="Large brand symbol area in navy"></div>
    <div class="person">
      <p class="person__name">Peter Castrell</p>
      <p class="person__role">President</p>
    </div>
    <ul class="contact">
      <li class="contact__item">
        <svg class="contact__icon" viewBox="0 0 24 24" aria-hidden="true">
          <path d="M6.6 10.8a15.1 15.1 0 0 0 6.6 6.6l2.2-2.2a1 1 0 0 1 1-.25 11.4 11.4 0 0 0 3.6.57 1 1 0 0 1 1 1V20a1 1 0 0 1-1 1A17 17 0 0 1 3 4a1 1 0 0 1 1-1h3.5a1 1 0 0 1 1 1c0 1.25.2 2.45.57 3.6a1 1 0 0 1-.25 1z"/>
        </svg>
        <span>(555) 204-6391</span>
      </li>
      <li class="contact__item">
        <svg class="contact__icon" viewBox="0 0 24 24" aria-hidden="true">
          <path d="M2 5h20v14H2z M3.5 6.5 12 13l8.5-6.5" fill="var(--navy)" stroke="#fff" stroke-width="1.6"/>
        </svg>
        <span>pc@thornvalegroup.example</span>
      </li>
    </ul>
  </section>
</main>
</body>
</html>
```